Medical Billing Company Needs a Business Card Design

We need a business card design for a Florida based medical billing company called 'Clinicians Keystone Solutions'. We specialize in providing revenue cycle management services to physician and therapist offices (we're basically their back-office processing partner for providing billing software, claims submissions, A/R follow-up and patient statements & collections. Our logo is red and blue-ish, so make sure that whatever other elements are used will match appropriately. Our current business card design has a too small font size. I'd like to project an image that shows we are modern & reliable. On a side note, I'm planning on using ZUB for printing these cards.

Target Market(s)

Office managers, physicians, therapists

Industry/Entity Type

Printing

Requirements
Must have
• Logo
Name of Employee
Phone
Fax
E-mail
Website

```html
<!DOCTYPE html>
<html lang="en">
<head>
<meta charset="utf-8">
<title>Clinicians Keystone Solutions – Business Cards</title>
<link rel="stylesheet" href="https://fonts.googleapis.com/css2?family=Source+Sans+3:wght@400;600;700&display=swap">
<style>
  :root {
    --page: #f1ede6;
    --card: #efe4cf;
    --card-edge: #d9ccb3;
    --crimson: #9b1b20;
    --navy: #272163;
    --white: #ffffff;
    --brand: #2e2a6b;
  }
  * { margin: 0; padding: 0; box-sizing: border-box; }
  html, body {
    width: 1200px; height: 1106px; overflow: hidden;
    background: var(--page);
    font-family: "Source Sans 3", "Myriad Pro", Arial, sans-serif;
  }
  .stage { position: relative; width: 1200px; height: 1106px; }
  .card {
    position: absolute; width: 617px; height: 351px;
    background: var(--card);
    border: 1px solid var(--card-edge);
    box-shadow: 0 6px 18px rgba(60, 40, 20, 0.12);
    overflow: hidden;
  }
  .card--front { left: 183px; top: 147px; }
  .card--back  { left: 286px; top: 619px; }

  .brand {
    position: absolute; left: 0; right: 0;
    display: flex; align-items: center; justify-content: center; gap: 10px;
    color: var(--brand);
    font-weight: 400; font-size: 27px; letter-spacing: 2.4px;
    text-transform: uppercase; white-space: nowrap;
  }
  .brand__square { width: 16px; height: 16px; background: var(--brand); flex: none; }
  .card--front .brand { top: 88px; }
  .card--back .brand { top: 95px; transform: scaleX(-1); opacity: 0.85; }

  .band-name {
    position: absolute; left: 0; right: 0; top: 205px; height: 39px;
    background: var(--crimson); color: var(--white);
    display: flex; align-items: center; justify-content: center;
  }
  .person { font-weight: 700; font-size: 19px; }
  .person__title { font-weight: 400; font-size: 15px; margin-left: 4px; }

  .band-contact {
    position: absolute; left: 0; right: 0; top: 250px; bottom: 0;
    background: var(--navy); color: var(--white);
    display: flex; flex-direction: column; align-items: center;
    padding-top: 10px; gap: 6px;
  }
  .contact-line { display: flex; align-items: center; gap: 7px; font-size: 15px; }
  .contact-item { display: flex; align-items: center; gap: 4px; }
  .contact-item svg { width: 13px; height: 13px; fill: var(--white); }
  .web-line { font-size: 15px; letter-spacing: 2.6px; }
  .address-line { font-size: 15px; letter-spacing: 0.8px; margin-top: 3px; }

  .card--back .band-name { top: 205px; }
  .card--back .band-contact {
    top: 251px; padding-top: 0; justify-content: center;
  }
  .web-large { font-size: 25px; letter-spacing: 2.4px; }
</style>
</head>
<body>
<main class="stage">
  <section class="card card--front" aria-label="Card front">
    <div class="brand"><span class="brand__square"></span>Clinicians Keystone</div>
    <div class="band-name">
      <span class="person">Your Name,</span><span class="person__title">Title</span>
    </div>
    <div class="band-contact">
      <div class="contact-line">
        <span class="contact-item">
          <svg viewBox="0 0 16 16" aria-hidden="true"><path d="M3.5 1.5l2.6 2.6-1.4 2.1c.9 2 2.6 3.7 4.6 4.6l2.1-1.4 2.6 2.6-1.6 2.3C7.3 14.5 1.5 8.7 1.2 3.1z"/></svg>
          123-456-0789
        </span>
        <span class="contact-item">
          <svg viewBox="0 0 16 16" aria-hidden="true"><path d="M4.5 0.5h7v15h-7zM6 2.5v9h4v-9zM7.3 12.7h1.4v1.4H7.3z" fill-rule="evenodd"/></svg>
          123-456-0789
        </span>
        <span class="contact-item">
          <svg viewBox="0 0 16 16" aria-hidden="true"><path d="M1 4l7 5 7-5v9H1zM1.5 3h13L8 7.6z"/></svg>
          info@clinicianskeystone.com
        </span>
      </div>
      <div class="web-line">www.clinicianskeystone.com</div>
      <div class="address-line">Street Name, City Name, State Zip Code</div>
    </div>
  </section>

  <section class="card card--back" aria-label="Card back">
    <div class="brand"><span class="brand__square"></span>Clinicians Keystone</div>
    <div class="band-name"></div>
    <div class="band-contact">
      <div class="web-large">www.clinicianskeystone.com</div>
    </div>
  </section>
</main>
</body>
</html>
```